Seeking a new website design for electrical contracting company

Brisket & Vane electrical contracting needs a new website for brisket-vane.example

We are looking for modern and something real cool with motion for a landing page. we have some cool images from our photo shoot. maybe even 3d motion our existing logo. we would like something we can edit with news and events and update a past project page. Also allow to take payment
stock images at
https://lorapellwinphotos.picvault-demo.example/Brisket-and-Vane

Target Market(s)

construction , home owners , business owners,

Industry/Entity Type

construction , electrical

Coding

Number of Pages Required

5+ page

Font styles to use
Serif
Sans Serif

Colors
0054AA
0677BA
7BADD7
CADEEF
E8F1F8
0094D4
00A9DD
6FCCEA
C7EBF8
E9F6FB
FFF300
FFF600
FEFA6F
FFFEC7
FFFEE8

Requirements
Must have
• excitement, motion, selling professionalism,

```html
<!DOCTYPE html>
<html lang="en">
<head>
<meta charset="utf-8">
<title>Brisket &amp; Vane Electrical Contractors</title>
<link href="https://fonts.googleapis.com/css2?family=Poppins:wght@400;500;600;700;800&display=swap" rel="stylesheet">
<style>
:root{
  --navy:#27336f;
  --navy-deep:#1f2a63;
  --orange:#f39a21;
  --ink:#222;
  --muted:#444;
  --white:#fff;
  --footer:#e6e6e8;
  --rule:#bfc0c6;
}
*{box-sizing:border-box;margin:0;padding:0}
html,body{width:1200px;height:3745px;overflow:hidden}
body{position:relative;background:var(--white);font-family:'Poppins',sans-serif;color:var(--ink)}
.abs{position:absolute}
.brand{font-weight:700;color:var(--navy);font-size:22px;display:flex;align-items:center;gap:10px;letter-spacing:.3px}
.brand-dot{width:30px;height:30px;border-radius:50%;background:var(--orange)}
.nav a{position:absolute;top:54px;font-size:15px;color:var(--ink);text-decoration:none;font-weight:500}
.nav .active{color:var(--navy);font-weight:600;border-bottom:2px solid var(--navy);padding-bottom:2px}
.btn{position:absolute;display:flex;align-items:center;justify-content:center;gap:8px;background:var(--navy);color:var(--white);border-radius:30px;font-weight:500;text-decoration:none}
.bolt{width:12px;height:20px}
.photo{position:absolute}
.hero-photo{left:0;top:125px;width:1200px;height:527px;background:linear-gradient(100deg,#e9eef4 0%,#c9d9e8 35%,#6f9ac6 60%,#3b6aa0 100%)}
.hero-title{left:115px;top:222px;font-size:42px;font-weight:700;line-height:54px;color:#2a2a2a}
.hero-title span{color:var(--navy);display:block}
.hero-sub{left:115px;top:344px;font-size:15px;line-height:28px;color:#222}
.eyebrow{left:636px;top:742px;display:flex;align-items:center;gap:16px;font-weight:600;font-size:16px;color:var(--navy)}
.eyebrow i{display:block;width:46px;height:3px;background:var(--navy)}
.about-title{left:636px;top:786px;font-size:28px;line-height:37px;color:#2a2a2a;font-weight:400}
.about-title b{color:var(--navy);font-weight:700}
.about-text{left:636px;top:872px;width:460px;font-size:15px;line-height:26.2px;color:#222}
.about-strong{left:636px;top:1038px;width:470px;font-size:15px;line-height:26px;font-weight:700}
.section-title{width:1200px;left:0;text-align:center;font-size:38px;font-weight:700}
.frame{position:absolute}
.dots{position:absolute;display:flex;gap:6px}
.dots i{display:block;width:14px;height:14px;border-radius:50%;background:var(--white)}
.card{position:absolute;border-radius:8px;background:#ececee;box-shadow:0 3px 10px rgba(0,0,0,.2);padding:0 22px}
.card h3{position:absolute;left:22px;top:102px;font-size:19px;color:var(--navy);font-weight:600}
.card p{position:absolute;left:24px;top:138px;font-size:13.5px;line-height:21px;color:#333}
.card.on{background:var(--navy)}
.card.on h3,.card.on p{color:var(--white)}
.card svg{position:absolute;left:22px;top:30px}
.news-card h4{position:absolute;font-size:17px;line-height:26px;font-weight:500}
.news-card p{position:absolute;font-size:13.5px;line-height:22px}
.pill{position:absolute;border-radius:16px;font-size:10px;display:flex;align-items:center;justify-content:center;font-weight:500}
.foot h5{position:absolute;font-size:18px;font-weight:600;color:var(--navy)}
.foot a{position:absolute;font-size:15px;color:#333;text-decoration:none}
.foot p{position:absolute;font-size:15px;color:#333}
.social{position:absolute;width:28px;height:28px;border-radius:50%;background:var(--navy)}
</style>
</head>
<body>

<!-- Header -->
<header>
  <div class="abs brand" style="left:62px;top:46px"><span class="brand-dot"></span>Brisket &amp; Vane</div>
  <nav class="nav">
    <a class="active" style="left:410px">HOME</a>
    <a style="left:516px">ABOUT US</a>
    <a style="left:652px">SERVICES</a>
    <a style="left:784px">TESTIMONIALS</a>
  </nav>
  <a class="btn" style="left:915px;top:38px;width:221px;height:52px;font-size:16px">SCHEDULE QUOTE
    <svg class="bolt" viewBox="0 0 12 20"><path d="M7 0L0 11h5l-2 9 9-12H7z" fill="var(--orange)"/></svg></a>
</header>

<!-- Hero -->
<section>
  <div class="photo hero-photo" role="img" aria-label="Smiling electrician in hard hat and hi-vis vest on the phone beside solar panels"></div>
  <h1 class="abs hero-title">POWERING YOUR<span>PROJECTS WITH PRECISION</span></h1>
  <p class="abs hero-sub">Expert Electrical Solutions for Homes,<br>Businesses &amp; Industrial Sites<br>Licensed • Insured • On Time • On Budget</p>
  <a class="btn" style="left:115px;top:458px;width:225px;height:50px;font-size:15px">VIEW OUR SERVICES
    <svg class="bolt" viewBox="0 0 12 20"><path d="M7 0L0 11h5l-2 9 9-12H7z" fill="var(--orange)"/></svg></a>
</section>

<!-- About -->
<section>
  <div class="abs" style="left:70px;top:742px;width:395px;height:433px;background:var(--orange);border-radius:4px"></div>
  <div class="photo" style="left:108px;top:774px;width:477px;height:419px;background:linear-gradient(135deg,#9fb8d0,#c8b58a 45%,#4d6a92);border-radius:6px" role="img" aria-label="Three electricians in hard hats reviewing plans beside solar panels"></div>
  <div class="abs eyebrow"><i></i>ABOUT US</div>
  <h2 class="abs about-title"><b>POWERING TRUST</b>, ONE<br>PROJECT AT A TIME</h2>
  <p class="abs about-text">we bring over [X] years of experience delivering safe, efficient, and code-compliant electrical work across residential, commercial, and industrial projects. From new construction wiring to service upgrades and emergency repairs, we’re committed to getting the job done right — the first time.</p>
  <p class="abs about-strong">Whether you’re building, remodeling, or just need an expert’s eye — we’re here to help power your next project.</p>
  <a class="btn" style="left:631px;top:1123px;width:226px;height:48px;font-size:15px">VIEW OUR SERVICES
    <svg class="bolt" viewBox="0 0 12 20"><path d="M7 0L0 11h5l-2 9 9-12H7z" fill="var(--orange)"/></svg></a>
</section>

<!-- Projects -->
<section>
  <svg class="abs" style="left:0;top:1280px" width="1200" height="780" viewBox="0 0 1200 780">
    <path d="M0 60 Q300 0 600 10 Q960 20 1200 100 L1200 765 Q960 700 700 705 Q300 712 0 740 Z" fill="var(--orange)"/>
  </svg>
  <h2 class="abs section-title" style="top:1350px;color:var(--white)">CHECKING OUR <span style="color:var(--navy)">PROJECTS</span></h2>
  <div class="frame" style="left:58px;top:1457px;width:313px;height:402px;background:var(--navy)"></div>
  <div class="photo" style="left:80px;top:1478px;width:313px;height:358px;background:linear-gradient(90deg,#f0a64a,#9a8a78 55%,#5a6470)" role="img" aria-label="Electrician in white hard hat installing a wall panel"></div>
  <div class="frame" style="left:477px;top:1457px;width:313px;height:402px;background:var(--white)"></div>
  <div class="photo" style="left:445px;top:1478px;width:313px;height:358px;background:linear-gradient(180deg,#5a6f86,#3e5878 50%,#d9dde2)" role="img" aria-label="Electrician on a ladder wiring a ceiling light fixture"></div>
  <div class="frame" style="left:854px;top:1457px;width:311px;height:402px;background:var(--navy)"></div>
  <div class="photo" style="left:822px;top:1478px;width:311px;height:358px;background:linear-gradient(135deg,#f0a64a,#8b7b68 45%,#333a40)" role="img" aria-label="Gloved hands testing a breaker panel"></div>
  <div class="dots" style="left:576px;top:1901px"><i style="background:var(--navy)"></i><i></i><i></i></div>
</section>

<!-- Services -->
<section>
  <h2 class="abs section-title" style="top:2082px;font-weight:500;color:var(--navy)">OUR ELECTRICAL <span style="color:var(--orange)">SERVICES</span></h2>
  <p class="abs" style="left:0;width:1200px;top:2152px;text-align:center;font-size:15px;line-height:25px">We offer a full range of electrical contracting services tailored to meet the needs of<br>homeowners, businesses, and builders alike. No job is too big or too small.</p>

  <div class="card" style="left:134px;top:2262px;width:281px;height:225px">
    <svg width="56" height="54" viewBox="0 0 56 54" fill="none" stroke="var(--navy)" stroke-width="2"><rect x="4" y="20" width="20" height="32"/><rect x="24" y="6" width="26" height="46"/><path d="M30 14h4M40 14h4M30 24h4M40 24h4M30 34h4M40 34h4M10 28h8M10 38h8M34 44h8v8h-8z"/></svg>
    <h3>Residential Services</h3>
    <p>New Home Wiring<br>Electrical Panel Upgrades Lighting<br>Installation(Indoor/Outdoor)</p>
  </div>
  <div class="card on" style="left:457px;top:2265px;width:276px;height:220px">
    <svg width="50" height="54" viewBox="0 0 50 54" fill="none" stroke="var(--white)" stroke-width="2"><rect x="4" y="22" width="16" height="30"/><rect x="20" y="4" width="26" height="48"/><path d="M26 12h4M36 12h4M26 22h4M36 22h4M26 32h4M36 32h4M9 30h6M9 40h6"/></svg>
    <h3 style="top:96px">Commercial Services</h3>
    <p style="top:132px">Tenant Build-Outs<br>Lighting Design &amp; Retrofits<br>Circuit Additions &amp; Upgrades</p>
  </div>
  <div class="card" style="left:785px;top:2262px;width:280px;height:225px">
    <svg width="54" height="56" viewBox="0 0 54 56" fill="none" stroke="var(--navy)" stroke-width="2"><path d="M4 54V26l12-8v8l12-8v8l12-8v36z"/><rect x="40" y="6" width="8" height="48"/><path d="M10 40h6M22 40h6M10 48h18"/></svg>
    <h3>Industrial Services</h3>
    <p>Heavy Equipment Wiring<br>Control Systems &amp; Automation<br>High-Voltage Installations</p>
  </div>
  <div class="dots" style="left:581px;top:2544px"><i style="background:var(--navy);width:17px;height:17px"></i><i style="background:#c9c9cc;width:11px;height:11px;margin-top:3px"></i></div>
</section>

<!-- News -->
<section class="news">
  <svg class="abs" style="left:0;top:2615px" width="1200" height="712" viewBox="0 0 1200 712">
    <path d="M0 80 Q200 10 600 10 Q1000 10 1200 80 L1200 620 Q1000 700 600 700 Q200 700 0 620 Z" fill="var(--navy)"/>
  </svg>
  <h2 class="abs section-title" style="top:2684px;font-size:32px;font-weight:500;color:var(--white)">OUR RECENT <span style="color:var(--orange);font-weight:700">NEWS</span></h2>

  <div class="news-card" style="color:var(--white)">
    <div class="photo" style="left:71px;top:2797px;width:312px;height:243px;background:linear-gradient(180deg,#8fb7e0,#c9d4dc 50%,#2f4f78)" role="img" aria-label="Engineer with tablet inspecting a solar panel field"></div>
    <h4 style="left:71px;top:3056px">1. 5 Signs Your Home Needs an<br>Electrical Panel Upgrade</h4>
    <p style="left:71px;top:3125px">Your electrical panel is the heart of your<br>home’s power system —</p>
    <div class="pill" style="left:73px;top:3196px;width:94px;height:29px;background:var(--white);color:var(--navy)">READ MORE</div>
  </div>

  <div class="abs" style="left:419px;top:2769px;width:369px;height:485px;background:var(--white);border-radius:20px"></div>
  <div class="news-card" style="color:var(--navy)">
    <div class="photo" style="left:448px;top:2797px;width:310px;height:243px;background:linear-gradient(90deg,#e5743a,#a38a7e 55%,#c8ccd2)" role="img" aria-label="Smiling electrician in orange jacket working on an outdoor meter box"></div>
    <h4 style="left:452px;top:3056px">2. Is Your Business Ready for an<br>Energy-Efficient Lighting Upgrade?</h4>
    <p style="left:452px;top:3125px;color:#444">Upgrading to LED or smart lighting can<br>save your business thousands</p>
    <div class="pill" style="left:450px;top:3193px;width:88px;height:29px;background:var(--navy);color:var(--white)">READ MORE</div>
  </div>

  <div class="news-card" style="color:var(--white)">
    <div class="photo" style="left:809px;top:2797px;width:310px;height:243px;background:linear-gradient(135deg,#3a4a68,#6f7d8c 55%,#9aa3a8)" role="img" aria-label="Technician in cap servicing a portable generator"></div>
    <h4 style="left:813px;top:3056px">3. How to Safely Use a Portable<br>Generator During Storm Season</h4>
    <p style="left:811px;top:3125px">Portable generators can be lifesavers —<br>but only if used correctly.</p>
    <div class="pill" style="left:810px;top:3193px;width:91px;height:29px;background:var(--white);color:var(--navy)">READ MORE</div>
  </div>
</section>

<!-- Footer -->
<footer class="foot">
  <div class="abs" style="left:0;top:3316px;width:1200px;height:429px;background:var(--footer);z-index:-1"></div>
  <div class="abs brand" style="left:112px;top:3412px;font-size:24px"><span class="brand-dot"></span>Brisket &amp; Vane</div>
  <svg class="abs" style="left:110px;top:3478px" width="16" height="20" viewBox="0 0 16 20"><path d="M8 0a7 7 0 0 0-7 7c0 5 7 13 7 13s7-8 7-13a7 7 0 0 0-7-7z" fill="var(--navy)"/><circle cx="8" cy="7" r="2.6" fill="var(--footer)"/></svg>
  <p style="left:138px;top:3477px">48 Alder Row</p>
  <p style="left:113px;top:3506px">Millbrook NH 03000</p>
  <p style="left:113px;top:3537px">www.brisket-vane.example</p>
  <span class="social" style="left:112px;top:3580px"></span>
  <span class="social" style="left:152px;top:3580px"></span>
  <span class="social" style="left:191px;top:3580px"></span>
  <span class="social" style="left:230px;top:3580px"></span>
  <span class="social" style="left:270px;top:3580px"></span>

  <h5 style="left:445px;top:3394px">Quick links</h5>
  <a style="left:445px;top:3437px">Home</a>
  <a style="left:445px;top:3476px">About Us</a>
  <a style="left:445px;top:3515px">Services</a>
  <a style="left:445px;top:3555px">Blog</a>
  <a style="left:445px;top:3594px">Contact Us</a>

  <h5 style="left:634px;top:3394px">Service Areas</h5>
  <a style="left:634px;top:3437px">Residential Services</a>
  <a style="left:634px;top:3476px">Commercial Services</a>
  <a style="left:634px;top:3515px">Industrial Services</a>
  <a style="left:634px;top:3555px">Emergency Services</a>

  <h5 style="left:880px;top:3394px">Connect With Us</h5>
  <svg class="abs" style="left:886px;top:3453px" width="22" height="16" viewBox="0 0 22 16"><rect width="22" height="16" rx="2" fill="var(--navy)"/><path d="M1 2l10 7 10-7" stroke="var(--footer)" stroke-width="1.6" fill="none"/></svg>
  <p style="left:918px;top:3449px">hello@brisket-vane.example</p>
  <svg class="abs" style="left:888px;top:3492px" width="18" height="18" viewBox="0 0 24 24"><path d="M6.6 10.8a15 15 0 0 0 6.6 6.6l2.2-2.2a1 1 0 0 1 1-.25 11.4 11.4 0 0 0 3.6.6 1 1 0 0 1 1 1V20a1 1 0 0 1-1 1A17 17 0 0 1 3 4a1 1 0 0 1 1-1h3.5a1 1 0 0 1 1 1c0 1.25.2 2.45.6 3.6a1 1 0 0 1-.25 1z" fill="var(--navy)"/></svg>
  <p style="left:918px;top:3490px">1-555-010-4477</p>
  <a class="btn" style="left:886px;top:3532px;width:167px;height:36px;font-size:14px;color:var(--white)">Schedule Quote</a>

  <div class="abs" style="left:0;top:3695px;width:1200px;height:1px;background:var(--rule)"></div>
  <p style="left:0;width:1200px;top:3710px;text-align:center;font-size:15px">Copyrights@ <b style="color:var(--navy)">Brisket &amp; Vane</b> - All Rights Reserved</p>
</footer>

</body>
</html>
```